Torvane Halbridge

Looking for modern business cards.
Clean contemporary design.
Similar to this.
https://www.plumvexa-search.example/imgres?imgurl=https%3A%2F%2Fimg.quorlint-cdn.example%2Fsleek_dark_metal_card_design_540.jpg&imgrefurl=https%3A%2F%2Fwww.quorlint-prints.example%2Fsleek_dark_metal_card_design-918273645501928374&q=modern%20business%20cards

But I'd like the blue to look metallic.

Business

```html
<!DOCTYPE html>
<html lang="en">
<head>
<meta charset="utf-8">
<title>Torvane Halbridge – Business Cards</title>
<link href="https://fonts.googleapis.com/css2?family=Roboto:wght@400;500&family=Roboto+Condensed:wght@400;700&display=swap" rel="stylesheet">
<style>
  :root{
    --backdrop:#e8e5e0;
    --paper:#fbfbfa;
    --ink:#3d4045;
    --brand-blue:#1f5a78;
    --brand-teal:#2aa3c9;
    --accent-red:#e2402c;
    --metal-dark:#163f58;
    --metal-mid:#2a6a8c;
    --metal-light:#5c97b6;
    --rule:#cfd2d4;
  }
  *{box-sizing:border-box;margin:0;padding:0}
  html,body{width:1200px;height:886px;overflow:hidden;background:var(--backdrop)}
  .canvas{position:relative;width:1200px;height:886px}
  .card{position:absolute;top:293px;width:520px;height:300px;border-radius:3px;overflow:hidden;
        box-shadow:0 10px 28px rgba(0,0,0,.18),0 2px 6px rgba(0,0,0,.12)}
  /* front */
  .card-front{left:50px;background:var(--paper)}
  .front-divider{position:absolute;left:0;top:0}
  .brand{position:absolute;left:42px;top:128px;width:220px;text-align:center}
  .brand-mark{display:flex;align-items:center;justify-content:center;gap:8px;white-space:nowrap;
        font-family:"Roboto Condensed",sans-serif;font-weight:700;font-size:25px;color:var(--brand-blue);letter-spacing:.2px}
  .brand-dot{width:12px;height:12px;border-radius:50%;background:var(--brand-teal);flex:none}
  .brand-tagline{margin-top:6px;font-family:"Roboto",sans-serif;font-size:7.5px;color:var(--brand-blue);letter-spacing:.6px;white-space:nowrap}
  .contact{position:absolute;left:300px;top:34px;width:210px;font-family:"Roboto",sans-serif;color:var(--ink)}
  .person-name{font-family:"Roboto Condensed",sans-serif;font-weight:700;font-size:19px;color:var(--brand-blue);letter-spacing:.3px}
  .person-role{font-family:"Roboto Condensed",sans-serif;font-size:14px;color:var(--brand-teal);margin-top:1px}
  .address{margin-top:14px;font-size:11.5px;line-height:1.45}
  .lines{margin-top:8px;list-style:none;font-size:11.5px;line-height:1.5}
  .lines li{display:flex;align-items:center;gap:8px;white-space:nowrap}
  .lines svg{width:11px;height:11px;flex:none;fill:var(--ink)}
  .front-band{position:absolute;left:0;bottom:0;width:100%;height:26px;background:var(--brand-blue);
        display:flex;align-items:center;justify-content:space-around;padding:0 20px}
  .band-ring{width:12px;height:12px;border-radius:50%;border:1.5px solid #fff}
  .band-dot{width:12px;height:12px;border-radius:50%;background:var(--accent-red)}
  /* back */
  .card-back{left:630px;
        background:
          linear-gradient(115deg,rgba(255,255,255,0) 30%,rgba(255,255,255,.16) 46%,rgba(255,255,255,0) 60%),
          linear-gradient(160deg,var(--metal-light) 0%,var(--metal-mid) 30%,var(--metal-dark) 62%,var(--metal-mid) 85%,var(--metal-light) 100%)}
  .back-brand{position:absolute;left:0;top:112px;width:100%;text-align:center}
  .back-brand .brand-mark{color:#fff;font-size:32px}
  .back-brand .brand-dot{background:#fff}
  .back-brand .brand-tagline{color:#cfe3ee}
  .back-web{position:absolute;left:0;bottom:26px;width:100%;text-align:center;
        font-family:"Roboto",sans-serif;font-size:11px;letter-spacing:1.5px;color:#e4eef4}
</style>
</head>
<body>
<main class="canvas">
  <article class="card card-front">
    <svg class="front-divider" width="520" height="300" aria-hidden="true">
      <line x1="285" y1="28" x2="285" y2="255" stroke="var(--rule)" stroke-width="1"/>
    </svg>
    <div class="brand">
      <div class="brand-mark"><span class="brand-dot"></span>Torvane Halbridge</div>
      <p class="brand-tagline">"STEADY PARTNERS FOR GROWING VENTURES"</p>
    </div>
    <div class="contact">
      <h1 class="person-name">DELIA MARROW</h1>
      <p class="person-role">CEO/FOUNDER</p>
      <p class="address">1420 Wrenfield Court<br>Larkspur Bay, Ostria 20418</p>
      <ul class="lines">
        <li><svg viewBox="0 0 24 24"><path d="M6.6 10.8a15.1 15.1 0 0 0 6.6 6.6l2.2-2.2a1 1 0 0 1 1-.25 11.4 11.4 0 0 0 3.6.57 1 1 0 0 1 1 1V20a1 1 0 0 1-1 1A17 17 0 0 1 3 4a1 1 0 0 1 1-1h3.5a1 1 0 0 1 1 1c0 1.25.2 2.45.57 3.6a1 1 0 0 1-.25 1z"/></svg>555 310 4827</li>
        <li><svg viewBox="0 0 24 24"><path d="M7 1h10a2 2 0 0 1 2 2v18a2 2 0 0 1-2 2H7a2 2 0 0 1-2-2V3a2 2 0 0 1 2-2zm0 3v14h10V4z"/></svg>555 729 1063</li>
        <li><svg viewBox="0 0 24 24"><path d="M6 2h9l3 3v4h2a2 2 0 0 1 2 2v9a2 2 0 0 1-2 2H4a2 2 0 0 1-2-2v-9a2 2 0 0 1 2-2h2zm2 2v5h8V6h-2V4zm-2 9v2h3v-2zm5 0v2h3v-2zm5 0v2h3v-2z"/></svg>555 846 2391</li>
        <li><svg viewBox="0 0 24 24"><path d="M2 4h20v16H2zm2 2v.5l8 5 8-5V6zm0 3v9h16V9l-8 5z"/></svg>hello@halbridge.example</li>
        <li><svg viewBox="0 0 24 24"><path d="M12 2a10 10 0 1 0 0 20 10 10 0 0 0 0-20zm6.9 6h-3a15 15 0 0 0-1.4-3.9A8 8 0 0 1 18.9 8zM12 4c.8 1.2 1.5 2.5 1.9 4h-3.8c.4-1.5 1.1-2.8 1.9-4zM4.3 14a8 8 0 0 1 0-4h3.4a16 16 0 0 0 0 4zm.8 2h3a15 15 0 0 0 1.4 3.9A8 8 0 0 1 5.1 16zm3-8h-3a8 8 0 0 1 4.4-3.9C8.8 5.3 8.4 6.6 8.1 8zM12 20c-.8-1.2-1.5-2.5-1.9-4h3.8c-.4 1.5-1.1 2.8-1.9 4zm2.3-6H9.7a14 14 0 0 1 0-4h4.6a14 14 0 0 1 0 4zm.3 5.9c.6-1.2 1.1-2.5 1.4-3.9h3a8 8 0 0 1-4.4 3.9zm1.7-5.9a16 16 0 0 0 0-4h3.4a8 8 0 0 1 0 4z"/></svg>www.halbridge.example</li>
      </ul>
    </div>
    <div class="front-band" aria-hidden="true">
      <span class="band-ring"></span><span class="band-ring"></span><span class="band-dot"></span><span class="band-ring"></span><span class="band-ring"></span>
    </div>
  </article>

  <article class="card card-back">
    <div class="back-brand">
      <div class="brand-mark"><span class="brand-dot"></span>Torvane Halbridge</div>
      <p class="brand-tagline">"STEADY PARTNERS FOR GROWING VENTURES"</p>
    </div>
    <p class="back-web">www.halbridge.example</p>
  </article>
</main>
</body>
</html>
```